Redesign website for small print company

Vindurgata is a small printing company in Iceland mainly servicing Students, schools, etc. We are also doing all kind of other jobs, like business cards, book printing, brochure printing etc. We are also selling books online.
Our website is: www.vindurgata.is
What we are looking for is:
- Web Design (Uncoded - PSD layout only)
- Mobile friendly design, using our current color scheme: Red, green, yellow and light gray.
- Clean simple design
- Simple, light and easy to use.
- More menu Items/drop down
Industry/Entity Type
Digital Printing
Number of Pages Required
5+ page
Requirements
Must have
- Easy navigation
- Designed for mobile
- Current color scheme (see logo)
Nice to have
- Icon based products

```html
<!DOCTYPE html>
<html lang="en">
<head>
<meta charset="utf-8">
<title>Vindurgata – Printing</title>
<link href="https://fonts.googleapis.com/css2?family=Roboto:wght@400;500;700&family=Open+Sans:wght@400;600&display=swap" rel="stylesheet">
<style>
:root{
  --red:#e31e24;
  --red-dark:#c8151b;
  --yellow:#f7e11b;
  --orange:#f39a1e;
  --green:#1e5a32;
  --green-deep:#17502b;
  --gray:#f3f3f3;
  --line:#d9d9d9;
  --text:#333;
  --muted:#555;
}
*{box-sizing:border-box;margin:0;padding:0}
html,body{width:1200px;height:3666px;overflow:hidden}
body{position:relative;background:#fff;font-family:"Open Sans",sans-serif;color:var(--text)}
.abs{position:absolute}
h1,h2,h3,h4,.nav,.btn{font-family:"Roboto",sans-serif}

.topbar{left:0;top:0;width:1200px;height:30px;background:var(--red);color:#fff;font-size:11px}
.topbar .flags{left:162px;top:9px;display:flex;gap:6px}
.topbar .flags span{width:16px;height:11px;display:block}
.topbar .contact{right:160px;top:7px;display:flex;gap:34px}

.header{left:0;top:30px;width:1200px;height:95px;background:#fff}
.brand{left:160px;top:28px;display:flex;align-items:center;gap:10px}
.brand .mark{width:34px;height:34px;background:var(--red)}
.brand .name{font-family:"Roboto",sans-serif;font-weight:700;font-size:28px;color:var(--text)}
.nav{left:620px;top:50px;display:flex;gap:34px;font-size:14px;font-weight:500;color:#333}
.nav .active{color:var(--red)}
.nav .caret{font-size:9px;margin-left:4px}
.icon-btn{top:42px;width:32px;height:32px;border-radius:50%}

.hero{left:0;top:125px;width:1200px;height:511px;background:linear-gradient(110deg,#4a4e52 0%,#8a8f94 30%,#c9c3bd 55%,#6b5a55 75%,#c9403a 100%)}
.hero-title{left:752px;top:313px;width:448px;height:54px;background:var(--red);color:#fff;font-family:"Roboto",sans-serif;font-weight:700;font-size:32px;padding:8px 22px;letter-spacing:.5px}
.hero-sub{left:752px;top:372px;width:448px;height:44px;background:var(--yellow);color:#333;font-size:18px;padding:10px 32px}
.dots{left:510px;top:605px;display:flex;gap:8px}
.dots span{width:40px;height:3px;background:rgba(255,255,255,.5)}
.dots span.on{background:#fff}

.section-title{width:1200px;text-align:center;font-weight:500;font-size:38px;color:#222}
.card{width:283px;height:293px;background:var(--gray);border:1px solid #e3e3e3;text-align:center;padding-top:30px}
.card svg{width:70px;height:80px}
.card h3{font-size:19px;font-weight:500;margin:8px 0 24px}
.card p{font-size:11px;line-height:22px;color:var(--muted);padding:0 40px}
.card .go{display:inline-flex;width:30px;height:30px;border-radius:50%;background:var(--green);margin-top:14px;align-items:center;justify-content:center}
.card .go.warm{background:linear-gradient(135deg,var(--yellow),var(--red))}

.wave{left:0;top:1418px;width:1200px;height:672px}
.books-title{left:0;top:1536px;color:#fff;z-index:2}
.book{width:208px;height:296px;background:#fff;text-align:center;padding-top:22px;box-shadow:0 2px 10px rgba(0,0,0,.15)}
.book .cover{width:78px;height:140px;margin:0 auto}
.book h4{font-weight:400;font-size:14px;margin-top:24px;color:#333}
.book .price{font-family:"Roboto",sans-serif;font-weight:700;font-size:18px;color:var(--red);margin-top:6px}
.book .btn{display:inline-block;margin-top:10px;background:var(--red);color:#fff;font-size:11px;font-weight:700;padding:6px 18px;border-radius:14px}
.arrow{color:#fff;font-size:34px;top:1762px;font-family:"Roboto",sans-serif}

.about-title{left:161px;top:2110px;font-size:36px;font-weight:500;color:#222}
.about-lead{left:161px;top:2196px;font-size:20px;color:var(--red);font-family:"Roboto",sans-serif}
.about-text{left:161px;top:2236px;width:285px;font-size:11.5px;line-height:20px;color:#444}
.about-text p+p{margin-top:14px}
.about-photo{left:452px;top:2200px;width:311px;height:244px;border:3px solid var(--red);background:linear-gradient(135deg,#3d4a57,#9aa4ad 50%,#5b6470)}
.about-box{left:773px;top:2200px;width:263px;height:244px;border:2px solid var(--green);padding:30px 26px;font-size:11.5px;line-height:20px;color:#444}
.about-box p+p{margin-top:14px}

.services{left:0;top:2566px;width:1200px;height:464px;background:radial-gradient(ellipse at 50% 50%,#fafafa 40%,#e6e6e6 100%)}
.service{top:2699px;width:160px;text-align:center}
.service .disc{width:136px;height:136px;border-radius:50%;margin:0 auto;display:flex;align-items:center;justify-content:center}
.service h4{margin-top:22px;font-size:16px;font-weight:700;color:#222}

.cta{left:0;top:3030px;width:1200px;height:299px;background:var(--green-deep);text-align:center;color:#fff}
.cta h2{font-size:36px;font-weight:500;margin-top:66px}
.cta p{width:640px;margin:22px auto 0;font-size:11.5px;line-height:22px;color:#e8efe9}
.cta .btn{display:inline-block;margin-top:22px;background:var(--yellow);color:#222;font-size:13px;font-weight:700;padding:10px 30px;border-radius:22px}
.rule{left:0;top:3329px;width:1200px;height:7px;background:linear-gradient(90deg,var(--yellow),var(--red))}

.footer{left:0;top:3336px;width:1200px;height:330px;background:radial-gradient(circle at 85% 40%,#f6e3f0 0%,#fbf3f8 30%,#fdfafc 60%,#f4f6fb 100%)}
.foot-brand{left:172px;top:3470px;font-family:"Roboto",sans-serif;font-weight:700;font-size:22px;color:#222;display:flex;align-items:center;gap:8px}
.foot-brand .mark{width:28px;height:28px;background:var(--red)}
.foot-col{top:3400px;font-size:11.5px;color:#444}
.foot-col h4{font-size:13px;font-weight:500;color:#333;margin-bottom:20px;letter-spacing:.3px}
.foot-col li{list-style:none;line-height:26px}
.social{display:flex;gap:14px;align-items:center}
.social span{width:20px;height:20px;border-radius:50%;background:#222;display:block}
.copy{left:0;top:3626px;width:1200px;text-align:center;font-size:11px;color:#444}
</style>
</head>
<body>

<div class="abs topbar">
  <div class="abs flags"><span style="background:#2a3f8f"></span><span style="background:#2b57a8"></span></div>
  <div class="abs contact"><span>&#9742; Tel: 555 0142</span><span>&#9993; verk@vindurgata.is</span><span>&#9719; Mon - Fri: 9-17</span></div>
</div>

<header class="abs header">
  <div class="abs brand"><span class="mark"></span><span class="name">VINDURGATA</span></div>
  <nav class="abs nav"><span class="active">Home</span><span>Services<span class="caret">&#9660;</span></span><span>Job submit</span><span>About Us</span></nav>
  <div class="abs icon-btn" style="left:964px;background:var(--yellow)">
    <svg width="32" height="32" viewBox="0 0 32 32"><circle cx="15" cy="15" r="5" fill="none" stroke="#333" stroke-width="2"/><line x1="19" y1="19" x2="22" y2="22" stroke="#333" stroke-width="2"/></svg>
  </div>
  <div class="abs icon-btn" style="left:1002px;background:var(--green)">
    <svg width="32" height="32" viewBox="0 0 32 32"><path d="M10 11h2l2 8h7l2-6h-10" fill="none" stroke="#fff" stroke-width="1.8"/><circle cx="15" cy="22" r="1.3" fill="#fff"/><circle cx="20" cy="22" r="1.3" fill="#fff"/></svg>
  </div>
</header>

<div class="abs hero" role="img" aria-label="Print workers inspecting a freshly printed sheet beside an industrial printer"></div>
<div class="abs hero-title">VINDURGATA</div>
<div class="abs hero-sub">Lorem ipsum dolor sit amet, consectetur</div>
<div class="abs dots"><span class="on"></span><span></span><span></span><span></span></div>

<h2 class="abs section-title" style="left:0;top:682px">Our Products</h2>

<div class="abs card" style="left:161px;top:760px">
  <svg viewBox="0 0 70 80" fill="none" stroke="#e31e24" stroke-width="2.5"><path d="M14 8h40v56H14z"/><path d="M22 20h24M22 30h24M22 40h14"/><circle cx="48" cy="58" r="8"/><path d="M44 65l-2 10 6-4 6 4-2-10"/></svg>
  <h3>Essays</h3>
  <p>Lorem ipsum dolor sit amet, consectet ur adipiscing elit, sed do eiusmod temod idunt ut labore et dolore magna.</p>
  <span class="go warm"><svg width="10" height="10" viewBox="0 0 10 10"><path d="M3 1l4 4-4 4" fill="none" stroke="#fff" stroke-width="2"/></svg></span>
</div>
<div class="abs card" style="left:458px;top:760px">
  <svg viewBox="0 0 70 80" fill="none" stroke="#e31e24" stroke-width="2.5"><rect x="16" y="14" width="38" height="58" rx="4"/><path d="M30 6h10v12H30z"/><circle cx="35" cy="38" r="8"/><path d="M24 60c2-8 20-8 22 0"/></svg>
  <h3>Business cards</h3>
  <p>Lorem ipsum dolor sit amet, consectet ur adipiscing elit, sed do eiusmod temod idunt ut labore et dolore magna.</p>
  <span class="go"><svg width="10" height="10" viewBox="0 0 10 10"><path d="M3 1l4 4-4 4" fill="none" stroke="#fff" stroke-width="2"/></svg></span>
</div>
<div class="abs card" style="left:755px;top:760px">
  <svg viewBox="0 0 70 80" fill="none" stroke="#e31e24" stroke-width="2.5"><path d="M12 10h32v56H12z"/><path d="M22 18h34v56H22z" fill="#f3f3f3"/><path d="M30 30h18M30 40h18M30 50h18M30 60h10"/></svg>
  <h3>Leaflets</h3>
  <p>Lorem ipsum dolor sit amet, consectet ur adipiscing elit, sed do eiusmod temod idunt ut labore et dolore magna.</p>
  <span class="go"><svg width="10" height="10" viewBox="0 0 10 10"><path d="M3 1l4 4-4 4" fill="none" stroke="#fff" stroke-width="2"/></svg></span>
</div>
<div class="abs card" style="left:161px;top:1068px">
  <svg viewBox="0 0 70 80" fill="none" stroke="#e31e24" stroke-width="2.5"><path d="M14 8h42v64H14z"/><path d="M22 8v64"/><path d="M36 8v20l5-4 5 4V8"/></svg>
  <h3>Bookprinting</h3>
  <p>Lorem ipsum dolor sit amet, consectet ur adipiscing elit, sed do eiusmod temod idunt ut labore et dolore magna.</p>
  <span class="go"><svg width="10" height="10" viewBox="0 0 10 10"><path d="M3 1l4 4-4 4" fill="none" stroke="#fff" stroke-width="2"/></svg></span>
</div>
<div class="abs card" style="left:458px;top:1068px">
  <svg viewBox="0 0 70 80" fill="none" stroke="#e31e24" stroke-width="2.5"><path d="M12 8h46v44H12z"/><path d="M20 18h14v12H20zM40 18h10M40 26h10M20 38h30"/><path d="M25 52l-6 22M45 52l6 22M35 52v22"/></svg>
  <h3>Posters</h3>
  <p>Lorem ipsum dolor sit amet, consectet ur adipiscing elit, sed do eiusmod temod idunt ut labore et dolore magna.</p>
  <span class="go"><svg width="10" height="10" viewBox="0 0 10 10"><path d="M3 1l4 4-4 4" fill="none" stroke="#fff" stroke-width="2"/></svg></span>
</div>
<div class="abs card" style="left:755px;top:1068px">
  <svg viewBox="0 0 70 80" fill="none" stroke="#e31e24" stroke-width="2.5"><path d="M12 14h46v48H12z"/><path d="M12 54h46M12 62c0 6 46 6 46 0"/><path d="M22 26h26M22 34h26M22 42h16"/></svg>
  <h3>Textbooks</h3>
  <p>Lorem ipsum dolor sit amet, consectet ur adipiscing elit, sed do eiusmod temod idunt ut labore et dolore magna.</p>
  <span class="go"><svg width="10" height="10" viewBox="0 0 10 10"><path d="M3 1l4 4-4 4" fill="none" stroke="#fff" stroke-width="2"/></svg></span>
</div>

<svg class="abs wave" viewBox="0 0 1200 672" preserveAspectRatio="none">
  <defs><linearGradient id="warm" x1="0" y1="0" x2="1" y2="0.3"><stop offset="0" stop-color="#f2b41c"/><stop offset=".45" stop-color="#f07a1e"/><stop offset="1" stop-color="#e31e24"/></linearGradient></defs>
  <path d="M0 70 C250 30 550 120 850 80 C1020 58 1130 25 1200 0 L1200 505 C1000 520 750 560 500 600 C300 630 120 650 0 672 Z" fill="url(#warm)"/>
</svg>
<h2 class="abs section-title books-title">Our Books</h2>
<div class="abs arrow" style="left:106px">&#8249;</div>
<div class="abs arrow" style="left:1074px">&#8250;</div>

<div class="abs book" style="left:161px;top:1613px">
  <div class="cover" role="img" aria-label="Cover of History of Ideas" style="background:linear-gradient(180deg,#f4f4f4 0 45%,#c8151b 45% 55%,#f4f4f4 55%)"></div>
  <h4>History of Ideas</h4><div class="price">4.900 kr</div><span class="btn">Buy Now</span>
</div>
<div class="abs book" style="left:384px;top:1613px">
  <div class="cover" role="img" aria-label="Cover of System Analysis" style="background:linear-gradient(180deg,#fafafa,#d9d9d9)"></div>
  <h4>System Analysis</h4><div class="price">5.900 kr</div><span class="btn">Buy Now</span>
</div>
<div class="abs book" style="left:607px;top:1613px">
  <div class="cover" role="img" aria-label="Cover of Academic Writing" style="background:linear-gradient(180deg,#8a6a1e,#4e3a14)"></div>
  <h4>Academic Writing</h4><div class="price">5.450 kr</div><span class="btn">Buy Now</span>
</div>
<div class="abs book" style="left:830px;top:1613px">
  <div class="cover" role="img" aria-label="Cover of Tölur og Gögn" style="background:linear-gradient(180deg,#e8468a,#f6d1e2)"></div>
  <h4>Tölur og Gögn</h4><div class="price">5.990 kr</div><span class="btn">Buy Now</span>
</div>

<h2 class="abs about-title">About Us</h2>
<div class="abs about-lead">Welcome to University</div>
<div class="abs about-text">
  <p>University education is a company located in the campus, which has specialized in the service of school staff, as well as providing general public printing.</p>
  <p>Higher education publishes seminars and first-class textbooks for courses, prints theses for lesson, as well as working on an unprecedented number of smaller pieces for students, teachers and organizations. These include brochures, reports, questionnaires, business cards, books, OCR scanning and more.</p>
</div>
<div class="abs about-photo" role="img" aria-label="Two staff members working at a printing machine"></div>
<div class="abs about-box">
  <p>Higher education is a tailored print shop. The Leaf is the official eco-label of the Nordic countries, which has created a foothold in this country and is known among consumers.</p>
  <p>University education is located at the corner of Hlíðargata and Norðurgata. (walked into Norðurgata)</p>
</div>

<div class="abs services" role="img" aria-label="Top-down view of a desk with people, coffee cups, papers and books"></div>
<div class="abs service" style="left:367px">
  <div class="disc" style="background:var(--red)"><svg width="70" height="60" viewBox="0 0 70 60" fill="none" stroke="#fff" stroke-width="2.5"><path d="M6 30L64 6 50 54 34 38z"/><path d="M34 38L64 6M34 38v14l8-8"/></svg></div>
  <h4>SENDA VERK</h4>
</div>
<div class="abs service" style="left:521px">
  <div class="disc" style="background:var(--yellow)"><svg width="60" height="60" viewBox="0 0 60 60" fill="none" stroke="#333" stroke-width="2.5"><path d="M30 8C16 8 6 18 6 30s10 22 22 22c4 0 5-3 3-6s0-6 4-6h6c8 0 13-5 13-12C54 16 44 8 30 8z"/><circle cx="18" cy="26" r="3"/><circle cx="26" cy="18" r="3"/><circle cx="38" cy="18" r="3"/><circle cx="44" cy="28" r="3"/></svg></div>
  <h4>HANNA VERK</h4>
</div>
<div class="abs service" style="left:678px">
  <div class="disc" style="background:var(--green)"><svg width="60" height="60" viewBox="0 0 60 60" fill="none" stroke="#fff" stroke-width="2.5"><path d="M12 50V10h10v40z"/><path d="M22 48l10-34 9 3-10 33"/><path d="M24 50l22-24 7 6-22 18z"/></svg></div>
  <h4>FA TILBOD</h4>
</div>

<section class="abs cta">
  <h2>Get Started!</h2>
  <p>Sed ut perspiciatis unde omnis iste natus error sit voluptatem accusantium doloremque laudantium, totam reaperiet ut perspiciatis unde omnis iste natus error sit voluptatem accusantium doloremque laudantium, totam rem aper</p>
  <span class="btn">CONTACT US</span>
</section>
<div class="abs rule"></div>

<footer class="abs footer"></footer>
<div class="abs foot-brand"><span class="mark"></span>VINDURGATA</div>
<div class="abs foot-col" style="left:415px"><h4>COMPANY</h4><ul><li>Sed ut perspiciatis</li><li>Commisteatsuit</li><li>Sed ut perspiciatis</li><li>Commisteatsuit</li><li>Perspiciatis unde</li></ul></div>
<div class="abs foot-col" style="left:562px"><h4>LINKS</h4><ul><li>Sed ut perspiciatis</li><li>Commisteatsuit</li><li>Sed ut perspiciatis</li><li>Commisteatsuit</li><li>Perspiciatis unde</li></ul></div>
<div class="abs foot-col" style="left:721px">
  <h4>CONNECT</h4>
  <div class="social">
    <svg width="24" height="18" viewBox="0 0 24 18"><rect x="1" y="1" width="22" height="16" fill="#222"/><path d="M1 1l11 9 11-9" fill="none" stroke="#fff" stroke-width="1.6"/></svg>
    <span></span><span></span><span></span>
  </div>
  <h4 style="margin-top:24px;margin-bottom:12px">POLICIES</h4>
  <ul><li>Privacy</li><li>Complaint and Feedback</li></ul>
</div>
<div class="abs foot-col" style="left:926px"><h4>OTHER LINKS</h4><ul><li>Sed ut perspiciatis</li><li>Sed ut perspiciatis</li><li>Commisteatsuit</li><li>Perspiciatis unde</li><li>Sed ut perspiciatis</li></ul></div>
<div class="abs copy">© 2018 All Rights are Reserved. Privacy Policy | Terms of Use | Contact</div>

</body>
</html>
```